Mastering Modern Vineyard Management

size of the ad - 8”x 10.75" plus 0.25" bleed
I would like an ad for a magazine that will stand out and make people want to read the ad.
The ad should not be crowded and people reading the ad will be able to read the text.
I would like it to be a creative and modern-day design.
the list of topics should not be the focus of the ad.
the text is attached.
If you decide to use people in the ad then please no ladies.
please note that leave over 1 inch for the bottom of the footer

```html
<!DOCTYPE html>
<html lang="en">
<head>
<meta charset="utf-8">
<title>Vineyard Course – Mastering Modern Vineyard Management</title>
<link href="https://fonts.googleapis.com/css2?family=Oswald:wght@600;700&family=Figtree:wght@300;400;500;600;700&family=Barlow+Semi+Condensed:wght@600;700&display=swap" rel="stylesheet">
<style>
  :root{
    --navy:#0d3560;
    --navy-mid:#1b4a7e;
    --mist:#c9d6e6;
    --paper:#f3f6fa;
    --yellow:#f6ef2c;
    --blue:#1a72b8;
    --orange:#e8521e;
    --ink:#222426;
    --band-grey:#e8e8e9;
    --white:#ffffff;
    --divider:#9aa3ad;
    --partner:#3f6f95;
  }
  *{margin:0;padding:0;box-sizing:border-box}
  html,body{width:935px;height:1200px;overflow:hidden;background:var(--white)}
  body{font-family:"Figtree",sans-serif;color:var(--ink)}
  .ad{width:935px;height:1200px;display:flex;flex-direction:column}

  .hero{height:628px;flex:0 0 628px;background:var(--navy);position:relative;overflow:hidden}
  .hero__title{position:absolute;top:58px;left:0;right:0;text-align:center;
    font-family:"Oswald",sans-serif;font-weight:700;font-size:78px;letter-spacing:1px;
    color:var(--yellow);line-height:1}
  .hero__backdrop{position:absolute;left:0;right:0;top:175px;bottom:0;
    background:linear-gradient(180deg,rgba(29,76,130,0) 0%,rgba(29,76,130,.7) 40%,var(--navy-mid) 100%)}
  .hero__scene{position:absolute;left:40px;right:40px;top:182px;bottom:0;
    background:linear-gradient(180deg,rgba(201,214,230,.25) 0%,rgba(201,214,230,.6) 35%,var(--mist) 65%,var(--paper) 100%)}

  .headline{height:114px;flex:0 0 114px;background:var(--band-grey);padding:11px 58px 0}
  .headline__title{font-weight:700;font-size:41px;color:var(--blue);line-height:1.15;letter-spacing:-.3px;white-space:nowrap}
  .headline__tagline{font-weight:500;font-size:33px;color:var(--ink);line-height:1.3;white-space:nowrap}

  .details{height:110px;flex:0 0 110px;background:var(--navy);display:flex;align-items:center;padding:0 58px;color:var(--white)}
  .details__col{line-height:1.18}
  .details__col--loc{width:290px}
  .details__col--time{flex:1;text-align:center}
  .details__col--date{width:162px;text-align:center}
  .details__divider{width:2px;height:76px;background:var(--divider)}
  .details__big{font-size:31px;font-weight:300;white-space:nowrap}
  .details__big strong{font-weight:600}
  .details__accent{font-size:30px;font-weight:700;color:var(--yellow);white-space:nowrap}
  .details__sub{font-size:17px;font-weight:500;color:var(--yellow);margin-top:2px;white-space:nowrap}
  .details__col--loc .details__big{font-size:30px}

  .offers{height:95px;flex:0 0 95px;display:flex;align-items:center;padding:0 58px;
    font-family:"Barlow Semi Condensed",sans-serif;font-weight:700;font-size:26px;line-height:1.2}
  .offers__item{white-space:nowrap}
  .offers__item--scholar{width:234px;color:var(--orange)}
  .offers__item--early{width:190px;padding-left:30px;color:var(--ink)}
  .offers__item--early span{color:var(--navy)}
  .offers__item--audience{padding-left:30px;color:var(--ink)}
  .offers__item--audience span{color:var(--navy)}
  .offers__divider{width:2px;height:62px;background:var(--divider)}

  .topics{height:124px;flex:0 0 124px;background:var(--band-grey);padding:18px 58px 0;
    display:grid;grid-template-columns:278px 165px 220px 1fr;font-size:16px}
  .topics__heading{font-family:"Barlow Semi Condensed",sans-serif;font-weight:700;font-size:20px;color:var(--blue);white-space:nowrap;margin-bottom:2px;line-height:1.1}
  .topics__list{list-style:none}
  .topics__list li{display:flex;align-items:flex-start;gap:6px;margin-bottom:6px;line-height:1.2;white-space:nowrap}
  .tick{flex:0 0 12px;width:12px;height:12px;margin-top:3px}

  .footer{flex:1;display:flex;align-items:center;padding:0 58px 20px;gap:20px}
  .org{flex:0 0 auto}
  .org__name{font-weight:700;font-size:17px;line-height:1.15;color:var(--blue)}
  .org__note{font-weight:600;font-size:10.5px;margin-top:5px;color:var(--blue)}
  .contact{flex:1;font-size:12.5px;line-height:1.6}
  .contact__row{display:flex;align-items:center;gap:5px}
  .contact svg{width:11px;height:11px;flex:0 0 11px}
  .contact__web{margin-left:16px;display:inline-flex;align-items:center;gap:5px}
  .contact__sponsor{font-size:10.5px;color:#444;margin-top:1px}
  .partner{flex:0 0 auto;text-align:right}
  .partner__mark{display:flex;align-items:center;gap:8px;justify-content:flex-end}
  .partner__square{width:26px;height:26px;background:var(--partner)}
  .partner__name{font-weight:500;font-size:18px;color:var(--partner);letter-spacing:.5px;line-height:1.1}
  .partner__note{font-size:9px;color:var(--partner);margin-top:5px}
</style>
</head>
<body>
<main class="ad">
  <section class="hero">
    <div class="hero__backdrop" role="img" aria-label="Faded blue rows of vines stretching to the horizon"></div>
    <div class="hero__scene" role="img" aria-label="Illustration of a bright vineyard landscape with rows of grapevines"></div>
    <h1 class="hero__title">VINEYARD COURSE</h1>
  </section>

  <section class="headline">
    <h2 class="headline__title">Mastering Modern Vineyard Management</h2>
    <p class="headline__tagline">Investing in knowledge is investing in opportunities</p>
  </section>

  <section class="details">
    <div class="details__col details__col--loc">
      <div class="details__big"><strong>Location:</strong> RIVERVALE</div>
      <div class="details__sub">Remote: for out of RIVERVALE Area</div>
    </div>
    <div class="details__divider"></div>
    <div class="details__col details__col--time">
      <div class="details__big">10 WEDNESDAY</div>
      <div class="details__accent">7:30 PM –9:30 PM</div>
    </div>
    <div class="details__divider"></div>
    <div class="details__col details__col--date">
      <div class="details__big">STARTING</div>
      <div class="details__accent">MARCH 8</div>
    </div>
  </section>

  <section class="offers">
    <div class="offers__item offers__item--scholar">LIMITED PARTIAL<br>SCHOLARSHIPS</div>
    <div class="offers__divider"></div>
    <div class="offers__item offers__item--early"><span>EARLY BIRD</span><br>SPECIAL</div>
    <div class="offers__divider"></div>
    <div class="offers__item offers__item--audience"><span>For those that started or</span><br>would like to grow wine grapes</div>
  </section>

  <section class="topics">
    <div>
      <div class="topics__heading">TOPICS: PARTIAL LISTING</div>
      <ul class="topics__list">
        <li><svg class="tick" viewBox="0 0 12 12"><circle cx="6" cy="6" r="6" fill="#1a72b8"/><path d="M3.3 6.2l1.8 1.8 3.6-3.7" stroke="#fff" stroke-width="1.5" fill="none"/></svg>Canopy strategies</li>
        <li><svg class="tick" viewBox="0 0 12 12"><circle cx="6" cy="6" r="6" fill="#1a72b8"/><path d="M3.3 6.2l1.8 1.8 3.6-3.7" stroke="#fff" stroke-width="1.5" fill="none"/></svg>Soil management</li>
      </ul>
    </div>
    <ul class="topics__list">
      <li><svg class="tick" viewBox="0 0 12 12"><circle cx="6" cy="6" r="6" fill="#1a72b8"/><path d="M3.3 6.2l1.8 1.8 3.6-3.7" stroke="#fff" stroke-width="1.5" fill="none"/></svg>Site selection</li>
      <li><svg class="tick" viewBox="0 0 12 12"><circle cx="6" cy="6" r="6" fill="#1a72b8"/><path d="M3.3 6.2l1.8 1.8 3.6-3.7" stroke="#fff" stroke-width="1.5" fill="none"/></svg>Irrigation</li>
      <li><svg class="tick" viewBox="0 0 12 12"><circle cx="6" cy="6" r="6" fill="#1a72b8"/><path d="M3.3 6.2l1.8 1.8 3.6-3.7" stroke="#fff" stroke-width="1.5" fill="none"/></svg>Pest control</li>
    </ul>
    <ul class="topics__list">
      <li><svg class="tick" viewBox="0 0 12 12"><circle cx="6" cy="6" r="6" fill="#1a72b8"/><path d="M3.3 6.2l1.8 1.8 3.6-3.7" stroke="#fff" stroke-width="1.5" fill="none"/></svg>Dealing with buyers</li>
      <li><svg class="tick" viewBox="0 0 12 12"><circle cx="6" cy="6" r="6" fill="#1a72b8"/><path d="M3.3 6.2l1.8 1.8 3.6-3.7" stroke="#fff" stroke-width="1.5" fill="none"/></svg>Harvest planning</li>
      <li><svg class="tick" viewBox="0 0 12 12"><circle cx="6" cy="6" r="6" fill="#1a72b8"/><path d="M3.3 6.2l1.8 1.8 3.6-3.7" stroke="#fff" stroke-width="1.5" fill="none"/></svg>Pruning</li>
    </ul>
    <ul class="topics__list">
      <li><svg class="tick" viewBox="0 0 12 12"><circle cx="6" cy="6" r="6" fill="#1a72b8"/><path d="M3.3 6.2l1.8 1.8 3.6-3.7" stroke="#fff" stroke-width="1.5" fill="none"/></svg>Tax fundamentals</li>
      <li><svg class="tick" viewBox="0 0 12 12"><circle cx="6" cy="6" r="6" fill="#1a72b8"/><path d="M3.3 6.2l1.8 1.8 3.6-3.7" stroke="#fff" stroke-width="1.5" fill="none"/></svg>Vineyard Legal<br>basics</li>
    </ul>
  </section>

  <footer class="footer">
    <div class="org">
      <div class="org__name">HARBOR CAREER<br>NETWORK</div>
      <div class="org__note">A NON-PROFIT OF MERIDIAN CIVIC LEAGUE</div>
    </div>
    <div class="contact">
      <div class="contact__row"><svg viewBox="0 0 12 12"><circle cx="6" cy="6" r="5.4" fill="none" stroke="#1a72b8"/><path d="M6 3a1.8 1.8 0 0 0-1.8 1.8C4.2 6.3 6 8.6 6 8.6s1.8-2.3 1.8-3.8A1.8 1.8 0 0 0 6 3z" fill="#1a72b8"/></svg>Rivervale- out of Rivervale Area</div>
      <div class="contact__row"><svg viewBox="0 0 12 12"><circle cx="6" cy="6" r="5.4" fill="none" stroke="#1a72b8"/><path d="M4 3.3l1 .2.4 1.3-.7.6a4 4 0 0 0 1.9 1.9l.6-.7 1.3.4.2 1-1 .8A5 5 0 0 1 3.2 4.3z" fill="#1a72b8"/></svg>555 014 2200 x 310</div>
      <div class="contact__row"><svg viewBox="0 0 12 12"><circle cx="6" cy="6" r="5.4" fill="none" stroke="#1a72b8"/><rect x="3.3" y="4" width="5.4" height="4" fill="none" stroke="#1a72b8" stroke-width=".9"/><path d="M3.3 4l2.7 2 2.7-2" fill="none" stroke="#1a72b8" stroke-width=".9"/></svg>info@harborcareer.org
        <span class="contact__web"><svg viewBox="0 0 12 12"><circle cx="6" cy="6" r="5.4" fill="none" stroke="#1a72b8"/><circle cx="6" cy="6" r="3" fill="none" stroke="#1a72b8" stroke-width=".8"/><path d="M3 6h6M6 3v6" stroke="#1a72b8" stroke-width=".8"/></svg>www.harborcareer.org</span></div>
      <div class="contact__sponsor">Sponsored in part by the Corwin Hale family foundation</div>
    </div>
    <div class="partner">
      <div class="partner__mark"><span class="partner__square"></span><span class="partner__name">STONEGATE<br>TITLE GROUP</span></div>
      <div class="partner__note">A Stonegate Property Services Company</div>
    </div>
  </footer>
</main>
</body>
</html>
```